Chimney Service company needs new business card design

We need a updated business card with our new logo added. We provide a full range of chimney services throughout Vermont and New Hampshire. The business card will be one sided and color. Attached is our current business card another document showing all the information we would like on the card.
We dont like a lot of flashy colors.... here is a link to our website to get an idea of our branding www.flueguardianvt.example

Target Market(s)

homeowners

Industry/Entity Type

Business

Contact Information for Business Card

See attached sheet for content.

Font styles to use
Serif
Sans Serif

Requirements
Must have
• all information provided on separate sheet
Should not have
• Additional information that may clogg up design

```html
<!DOCTYPE html>
<html lang="en">
<head>
<meta charset="utf-8">
<title>Flue Guardian – Business Card</title>
<link rel="stylesheet" href="https://fonts.googleapis.com/css2?family=Cinzel:wght@400;600&family=Lato:wght@400;700&family=Arimo:wght@400&display=swap">
<style>
  :root {
    --backdrop: #474747;
    --card: #ffffff;
    --brand-red: #8f0a0a;
    --charcoal: #333333;
    --ink: #222222;
    --rule: #e4e4e4;
    --white: #ffffff;
  }
  * { box-sizing: border-box; margin: 0; padding: 0; }
  html, body { width: 1200px; height: 900px; overflow: hidden; }
  body { background: var(--backdrop); position: relative; font-family: "Lato", sans-serif; color: var(--ink); }

  .card {
    position: absolute; top: 306px; width: 439px; height: 271px;
    background: var(--card); border-radius: 11px; overflow: hidden;
  }
  .card--front { left: 150px; }
  .card--back { left: 608px; }

  /* Front */
  .brand-mark {
    position: absolute; left: 222px; top: 31px; width: 66px; height: 63px;
    left: 72px; border: 5px solid var(--charcoal);
  }
  .brand-name {
    position: absolute; left: 22px; width: 166px; top: 108px; text-align: center;
    font-family: "Cinzel", serif; font-weight: 400; font-size: 18px; color: var(--ink); letter-spacing: 0.3px;
  }
  .brand-est {
    position: absolute; left: 22px; width: 166px; top: 128px; text-align: center;
    font-family: "Cinzel", serif; font-size: 9px; color: var(--ink); letter-spacing: 1px;
  }
  .divider { position: absolute; left: 22px; right: 22px; top: 160px; height: 1px; background: var(--rule); }

  .contact-list { position: absolute; left: 22px; top: 198px; list-style: none; }
  .contact-list li { display: flex; align-items: center; height: 16px; font-size: 13px; }
  .contact-list svg { width: 12px; height: 12px; margin-right: 5px; flex: none; }

  .service-list { position: absolute; left: 223px; top: 168px; list-style: none; }
  .service-list li { display: flex; align-items: center; height: 16px; font-size: 13px; }
  .service-list li::before {
    content: ""; width: 6px; height: 6px; background: var(--brand-red); margin-right: 6px; flex: none;
  }

  /* Back */
  .chimney-art { position: absolute; left: 0; top: 0; width: 145px; height: 100%; background: var(--brand-red); }
  .promise {
    position: absolute; right: 34px; top: 107px; text-align: right;
    font-family: "Cinzel", serif; font-size: 14px; line-height: 22px; color: var(--ink); letter-spacing: 0.4px;
  }
  .promise .sep { color: var(--brand-red); padding: 0 4px; }
  .name-band {
    position: absolute; left: 160px; right: 0; top: 173px; bottom: 0; background: var(--charcoal);
    color: var(--white); text-align: center;
  }
  .name-band .band-name {
    position: absolute; left: 0; right: 0; top: 14px;
    font-family: "Cinzel", serif; font-weight: 400; font-size: 22px; letter-spacing: 0.4px;
  }
  .name-band .band-est {
    position: absolute; left: 0; right: 0; top: 40px;
    font-family: "Cinzel", serif; font-size: 11px; letter-spacing: 1px;
  }
  .name-band .region {
    position: absolute; left: 0; right: 0; top: 57px;
    font-family: "Arimo", sans-serif; font-size: 12px;
  }
</style>
</head>
<body>
  <section class="card card--front">
    <div class="brand-mark"></div>
    <div class="brand-name">FLUE GUARDIAN</div>
    <div class="brand-est">INC 1989</div>
    <div class="divider"></div>

    <ul class="contact-list">
      <li>
        <svg viewBox="0 0 12 12"><rect width="12" height="12" fill="#8f0a0a"/><path d="M3.2 2.5l1.5 0 .6 2-1 .8a5 5 0 0 0 2.4 2.4l.8-1 2 .6v1.5c0 .4-.3.7-.7.7A6.6 6.6 0 0 1 2.5 3.2c0-.4.3-.7.7-.7z" fill="#fff"/></svg>
        802-555-0147
      </li>
      <li>
        <svg viewBox="0 0 12 12"><rect width="12" height="12" fill="#8f0a0a"/><rect x="2.5" y="3.5" width="7" height="5" fill="none" stroke="#fff" stroke-width="1"/><path d="M2.5 3.5l3.5 3 3.5-3" fill="none" stroke="#fff" stroke-width="1"/></svg>
        info@flueguardianvt.example
      </li>
      <li>
        <svg viewBox="0 0 12 12"><rect width="12" height="12" fill="#8f0a0a"/><path d="M6 2a2.8 2.8 0 0 0-2.8 2.8C3.2 7 6 10 6 10s2.8-3 2.8-5.2A2.8 2.8 0 0 0 6 2z" fill="#fff"/><circle cx="6" cy="4.8" r="1" fill="#8f0a0a"/></svg>
        www.flueguardianvt.example
      </li>
    </ul>

    <ul class="service-list">
      <li>Full Masonry Services</li>
      <li>Historic chimney restoration</li>
      <li>Stainless steel liners</li>
      <li>New Chimney installations</li>
      <li>Guild Certified Chimney sweeps</li>
    </ul>
  </section>

  <section class="card card--back">
    <div class="chimney-art" role="img" aria-label="Large chimney and flame illustration in red and white"></div>
    <p class="promise">
      Fully Insured<span class="sep">|</span>Free Estimates<br>
      Family owned and operated
    </p>
    <div class="name-band">
      <div class="band-name">FLUE GUARDIAN</div>
      <div class="band-est">INC 1989</div>
      <div class="region">Serving VT and New Hampshire since 1989</div>
    </div>
  </section>
</body>
</html>
```